Veldmark Supplies Business Card

Professional business card that stand out to our potential customers. Front and back with clean modern design

Industry/Entity Type

Oil and gas

Contact Information for Business Card

Name, address, website , office phone and cell number

Requirements
Must have
• Editable files for each employee

```html
<!DOCTYPE html>
<html lang="en">
<head>
<meta charset="utf-8">
<title>Veldmark Supplies Business Card</title>
<link rel="stylesheet" href="https://fonts.googleapis.com/css2?family=Poppins:wght@400;600&display=swap">
<style>
  :root {
    --bg: #e3e7e9;
    --red: #e8242a;
    --blue: #15aed3;
    --ink: #1c1c1c;
    --white: #ffffff;
    --peach: #f6d9c4;
  }
  * { margin: 0; padding: 0; box-sizing: border-box; }
  html, body { width: 1200px; height: 960px; overflow: hidden; background: var(--bg); font-family: "Poppins", sans-serif; }
  .card {
    position: absolute; left: 250px; width: 701px; height: 401px;
    border-radius: 30px; overflow: hidden;
  }
  .card-front { top: 60px; }
  .front-pattern {
    position: absolute; inset: 0;
    background: linear-gradient(225deg, var(--peach) 0%, #e9806a 30%, var(--red) 62%);
  }
  .card-back { top: 500px; background: var(--white); }
  .edge-band { position: absolute; right: 0; top: 0; width: 25px; height: 100%; }
  .edge-band .band-blue { position: absolute; top: 0; left: 0; right: 0; height: 62px; background: var(--blue); }
  .edge-band .band-red { position: absolute; top: 67px; bottom: 0; left: 0; right: 0; background: var(--red); }
  .person { position: absolute; right: 32px; top: 27px; text-align: right; }
  .person-name { font-size: 33px; line-height: 1.1; color: var(--red); font-weight: 400; }
  .person-name strong { font-weight: 600; }
  .person-title { font-size: 17px; color: var(--blue); margin-top: 2px; }
  .brand {
    position: absolute; left: 25px; top: 262px; width: 282px;
    display: flex; align-items: center; justify-content: center; gap: 10px;
  }
  .brand-mark { width: 18px; height: 18px; background: var(--red); }
  .brand-name { font-size: 24px; font-weight: 600; color: var(--red); }
  .address { position: absolute; right: 32px; top: 213px; text-align: right; font-size: 17px; line-height: 23px; color: var(--ink); }
  .contacts { position: absolute; right: 32px; top: 282px; list-style: none; }
  .contacts li { display: flex; align-items: center; justify-content: flex-end; gap: 8px; font-size: 17px; line-height: 24px; color: var(--ink); }
  .contacts svg { width: 16px; height: 16px; flex: none; }
</style>
</head>
<body>
  <section class="card card-front">
    <div class="front-pattern" role="img" aria-label="Repeating pattern of the company monogram on red, fading to light peach toward the top right"></div>
  </section>

  <section class="card card-back">
    <div class="edge-band"><div class="band-blue"></div><div class="band-red"></div></div>

    <div class="person">
      <p class="person-name"><strong>Marta</strong> Kovarik</p>
      <p class="person-title">Co-Founder &amp; CEO</p>
    </div>

    <div class="brand">
      <span class="brand-mark"></span>
      <span class="brand-name">Veldmark Supplies</span>
    </div>

    <p class="address">1840 Cedar Ridge Blvd. Suite 310<br>Abilene, TX 79601</p>

    <ul class="contacts">
      <li>(325) 614-0392
        <svg viewBox="0 0 24 24" fill="none" stroke="#15aed3" stroke-width="2.4" stroke-linecap="round"><path d="M5 3h4l2 5-3 2a11 11 0 0 0 6 6l2-3 5 2v4a2 2 0 0 1-2 2A17 17 0 0 1 3 5a2 2 0 0 1 2-2z"/></svg>
      </li>
      <li>(325) 614-0471
        <svg viewBox="0 0 24 24" fill="none" stroke="#e8242a" stroke-width="2.4"><rect x="6" y="2" width="12" height="20" rx="2"/></svg>
      </li>
      <li>www.website.com
        <svg viewBox="0 0 24 24" fill="none" stroke="#15aed3" stroke-width="2.2"><circle cx="12" cy="12" r="10"/><path d="M2 12h20M12 2c3 3 3 17 0 20M12 2c-3 3-3 17 0 20"/></svg>
      </li>
      <li>info@website.com
        <svg viewBox="0 0 24 24" fill="none" stroke="#e8242a" stroke-width="2.2" stroke-linejoin="round"><rect x="3" y="7" width="18" height="14" rx="1"/><path d="M3 8l9 7 9-7"/></svg>
      </li>
    </ul>
  </section>
</body>
</html>
```